Coastline Premier Retreats Business Card Design

Design a business card for Coastline Premier Retreats. Look at the website for colors and reference. Card should have logo, name, title, office number, mobile number, email, URL and a tagline like, "Luxury Hotel & Resort Email Marketing" (This might change).

https://www.coastlinepremierretreats.example

The rest I will leave up to your imagination.

Contact Information for Business Card

Logo, name, title, office number, mobile number, email, URL and a tagline like, "Luxury Hotel & Resort Email Marketing" (This might change).

```html
<!DOCTYPE html>
<html lang="en">
<head>
<meta charset="utf-8">
<title>Coastline Premier Retreats – Business Card</title>
<link rel="stylesheet" href="https://fonts.googleapis.com/css2?family=Arimo:wght@400;700&display=swap">
<style>
  :root {
    --backdrop: #2b2b2b;
    --card: #1b1b1b;
    --accent: #e8761c;
    --ink: #f2f2f2;
  }
  * { margin: 0; padding: 0; box-sizing: border-box; }
  html, body { width: 1200px; height: 1059px; overflow: hidden; }
  body {
    position: relative;
    background: var(--backdrop);
    font-family: "Arimo", Arial, sans-serif;
    color: var(--ink);
  }
  .card {
    position: absolute;
    background: var(--card);
    box-shadow: 0 14px 30px rgba(0,0,0,.55);
  }
  .card-front { left: 257px; top: 89px; width: 687px; height: 390px; }
  .card-back  { left: 253px; top: 546px; width: 694px; height: 394px; }

  .frame {
    position: absolute;
    left: 23px; top: 22px; width: 640px; height: 336px;
    overflow: visible;
  }
  .tagline {
    position: absolute;
    left: 0; right: 0; top: 345px;
    text-align: center;
    font-size: 17px;
    color: var(--accent);
    letter-spacing: .1px;
  }

  .identity {
    position: absolute;
    right: calc(687px - 315px);
    top: 136px;
    text-align: right;
    white-space: nowrap;
  }
  .person-name {
    font-size: 31px; font-weight: 700; color: var(--accent);
    line-height: 36px; letter-spacing: .3px;
  }
  .person-title { font-size: 17px; line-height: 20px; margin-bottom: 7px; letter-spacing: .3px; }
  .address { font-size: 16.5px; line-height: 21px; font-style: normal; }

  .divider {
    position: absolute;
    left: 340px; top: 148px; width: 1px; height: 92px;
    background: var(--accent);
  }

  .contact-list {
    position: absolute;
    left: 369px; top: 147px;
    list-style: none;
  }
  .contact-item {
    display: flex; align-items: center;
    height: 26px;
    font-size: 15.5px;
    white-space: nowrap;
  }
  .contact-icon { width: 12px; height: 12px; margin-right: 7px; flex: none; }

  .brand-name {
    position: absolute;
    left: 0; right: 0; top: 182px;
    display: flex; justify-content: center; align-items: center; gap: 14px;
    font-size: 30px; font-weight: 700; letter-spacing: 1.5px;
    text-transform: uppercase; color: var(--ink);
  }
  .brand-mark { width: 14px; height: 14px; background: var(--accent); }
</style>
</head>
<body>

<section class="card card-front">
  <svg class="frame" viewBox="0 0 640 336" aria-hidden="true">
    <polyline points="155,335 1,335 1,1 639,1 639,335 485,335"
      fill="none" stroke="var(--accent)" stroke-width="2"/>
  </svg>

  <div class="identity">
    <h1 class="person-name">MARCUS ELLERY</h1>
    <p class="person-title">CEO/Founder</p>
    <address class="address">PO Box, 48 Harbor Lane<br>Bayview, CA 90210</address>
  </div>

  <div class="divider"></div>

  <ul class="contact-list">
    <li class="contact-item">
      <svg class="contact-icon" viewBox="0 0 12 12" aria-hidden="true"><rect x="3" y="0.5" width="6" height="11" rx="1" fill="none" stroke="var(--accent)" stroke-width="1.2"/><circle cx="6" cy="9.5" r=".8" fill="var(--accent)"/></svg>
      555.014.2200
    </li>
    <li class="contact-item">
      <svg class="contact-icon" viewBox="0 0 12 12" aria-hidden="true"><path d="M1 4.5 Q6 0.5 11 4.5 L9.5 6 L8 5 L8 4 Q6 3 4 4 L4 5 L2.5 6 Z" fill="var(--accent)"/><rect x="2.5" y="6.5" width="7" height="4.5" rx=".8" fill="var(--accent)"/></svg>
      +34 600 000 417
    </li>
    <li class="contact-item">
      <svg class="contact-icon" viewBox="0 0 12 12" aria-hidden="true"><path d="M1 5 L6 1.5 L11 5 L11 11 L1 11 Z" fill="var(--accent)"/><path d="M1 5 L6 8.5 L11 5" fill="none" stroke="var(--card)" stroke-width="1"/></svg>
      info@coastlinepremierretreats.example
    </li>
    <li class="contact-item">
      <svg class="contact-icon" viewBox="0 0 12 12" aria-hidden="true"><circle cx="6" cy="6" r="5.2" fill="var(--accent)"/><path d="M1.2 6 H10.8 M6 0.8 Q3 6 6 11.2 M6 0.8 Q9 6 6 11.2" fill="none" stroke="var(--card)" stroke-width=".8"/></svg>
      www.coastlinepremierretreats.example
    </li>
  </ul>

  <p class="tagline">Luxury Hotel &amp; Resort Email Marketing</p>
</section>

<section class="card card-back">
  <div class="brand-name"><span class="brand-mark"></span>Coastline Premier Retreats</div>
</section>

</body>
</html>
```